Dietary supplement, Clean and simple.

Hi,
I’d like to talk about the project,

About us:
We are a dietary supplement (Vitamins, Minerals, amino acids etc.) company.
The goal is to have about 25 products at the end of this year. However, for this goal to be achieved we need a good label design to make our products represent our company values.
I’ll be here every day supporting your questions, we are fully committed to making the highest/best quality/customer experience possible.

About the design and our values:
- Professional (We are in the industry of professionalism and expertise. I would love to show we are competent at this, Id. Like to have the labels looks like we have done our research.)
- Efficient (White spacing, good use of the space available.)
- Simple (Straight forward, in 5 seconds they have to know what the product they have is/how functions. We’re trying to simplify it for the consumer.
- No distractions (the only visually “distracting” factor can be the vector art.)

The guidelines:
The goal is to have a universal design, with one element that changes (Vector art). I’ll attach a file/multiple files I think can show some visuals on what I’m looking for, and what parts of the design I think are good/bad.

Label size: 69x155mm (Front is 77.5mm)

Design whatever you think fits our image. You’re the design expert, all I care about is that it fits our company standards/image.

Use this color/font.
Font: Sans Serif
Main company color is Mind green #237D62 (Use this color for something in the design.)

What I thought would be cool/might looks ugly, who knows:
1. The front of the label: Should have 1 vector art, preferably in the top right corner. (That looks good in multiple colors. The vector can have multiple areas to color, I would prefer 2 main colors in the vector art. The interchangeable colors are used for multiple kinds of products.)
2. Text/product information on the left. The text that will have to be displayed:
- Product name for instance “Magnesium + B6”
- Description for the product for instance “Magnesium with ginger taste”
- Company name or logo. (Add ® behind it. We are soon to be trademark registered.)
3. We need to show the "daily intake" amount on the front and also the amount in the complete bottle. For instance, “Daily intake 1 capsule, 60 capsules”.
• You don’t have to design the backside of the label. After I chose a design, I’d like to chat and give specific information on what areas need to be assigned where. (Too complex because of the law.)
Updates

Hi, Please make the deadline 31 days total. I want designers to have the time to design. And not be rushed to finish it.

I want to extend the deadline because i feel like a slightly more medical look would be interesting. Hope you can come up with something!!

Target Market(s)

Dietary supplement consumers

Industry/Entity Type

Dietary supplements

Font styles to use
Sans Serif

Colors

Designer to choose colors to be used in the design.

Requirements
Must have
• Trademark icon "®" has to be at the top right after the company logo(text of logo)/name.

```html
<!DOCTYPE html>
<html lang="en">
<head>
<meta charset="utf-8">
<title>Magnesium + B6 — Front Label</title>
<link rel="stylesheet" href="https://fonts.googleapis.com/css2?family=IBM+Plex+Sans:wght@400;500;600&display=swap">
<style>
  :root {
    --mind-green: #237d62;
    --ink: #262626;
    --ink-soft: #555555;
    --ink-muted: #6a6a6a;
    --paper: #ffffff;
    --backdrop: #efefef;
    --grad-pink: #e9b3c4;
    --grad-mauve: #9a6a9c;
    --grad-indigo: #3b3a8a;
    --grad-periwinkle: #8d8fc4;
  }
  * { box-sizing: border-box; margin: 0; padding: 0; }
  html, body {
    width: 1200px; height: 1200px; overflow: hidden;
    background: var(--backdrop);
    font-family: "IBM Plex Sans", Arial, sans-serif;
    color: var(--ink);
  }
  .label-front {
    position: absolute;
    left: 170px; top: 160px;
    width: 860px; height: 880px;
    background: var(--paper);
    box-shadow: 0 10px 40px rgba(0,0,0,0.08);
  }
  .product-swatch {
    position: absolute;
    left: 64px; top: 64px;
    width: 240px; height: 380px;
    background:
      linear-gradient(35deg, var(--grad-indigo) 0%, var(--grad-mauve) 45%, transparent 80%),
      linear-gradient(200deg, var(--grad-pink) 0%, var(--grad-periwinkle) 100%);
  }
  .company-mark {
    position: absolute;
    right: 64px; top: 70px;
    display: flex; align-items: center; gap: 10px;
    font-size: 26px; font-weight: 600;
    color: var(--mind-green);
    letter-spacing: 0.04em;
  }
  .company-mark .dot {
    width: 14px; height: 14px; border-radius: 50%;
    background: var(--mind-green);
  }
  .product-info {
    position: absolute;
    left: 64px; top: 478px;
    width: 720px;
  }
  .brand-line {
    font-size: 30px; font-weight: 400;
    letter-spacing: 0.04em;
    color: var(--ink);
  }
  .brand-line sup { font-size: 16px; margin-left: 6px; vertical-align: 10px; }
  .product-name {
    margin-top: 8px;
    font-size: 66px; font-weight: 600;
    line-height: 1.05;
    color: var(--ink);
  }
  .product-name .plus { color: var(--ink-soft); font-weight: 500; }
  .accent-bar {
    margin-top: 24px;
    width: 240px; height: 5px;
    background: linear-gradient(90deg, var(--grad-pink), var(--grad-indigo));
  }
  .product-description {
    margin-top: 22px;
    font-size: 34px; font-weight: 400;
    line-height: 1.2;
    color: var(--ink-soft);
  }
  .divider {
    position: absolute;
    left: 64px; right: 64px; top: 780px;
    border-top: 2px dashed #b9c9c2;
  }
  .pack-count {
    position: absolute;
    left: 64px; top: 806px;
    display: flex; align-items: center; gap: 14px;
  }
  .pack-count .count-text { font-size: 18px; line-height: 1.2; color: var(--ink-muted); letter-spacing: 0.03em; }
  .pack-count .count-text strong { color: var(--mind-green); font-weight: 600; display: block; }
  .daily-intake {
    position: absolute;
    right: 64px; top: 800px;
    display: flex; align-items: stretch; gap: 12px;
    text-align: right;
  }
  .daily-intake .intake-text { font-size: 18px; line-height: 1.25; color: var(--ink-muted); letter-spacing: 0.03em; }
  .daily-intake .intake-text strong { color: var(--mind-green); font-weight: 600; display: block; }
  .daily-intake .rule { width: 2px; background: var(--mind-green); }
</style>
</head>
<body>
  <main class="label-front">
    <div class="product-swatch" aria-hidden="true"></div>

    <div class="company-mark">
      <span class="dot"></span>
      <span>HALVARD</span>
    </div>

    <section class="product-info">
      <p class="brand-line">HALVARD WELLNESS<sup>®</sup></p>
      <h1 class="product-name">Magnesium <span class="plus">+ B6</span></h1>
      <div class="accent-bar"></div>
      <p class="product-description">Magnesium with<br>ginger taste</p>
    </section>

    <div class="divider"></div>

    <div class="pack-count">
      <svg width="26" height="46" viewBox="0 0 26 46" aria-hidden="true">
        <rect x="2" y="2" width="22" height="42" rx="11" fill="none" stroke="#237d62" stroke-width="2.5"/>
        <line x1="2" y1="23" x2="24" y2="23" stroke="#237d62" stroke-width="2.5"/>
      </svg>
      <p class="count-text"><strong>60</strong>CAPSULES</p>
    </div>

    <div class="daily-intake">
      <p class="intake-text">DAILY INTAKE<strong>1 CAPSULE</strong></p>
      <span class="rule"></span>
    </div>
  </main>
</body>
</html>
```